co working space / serviced office/ business centre

Brevlo - brevlo.in, is a very young brand bieng run by 3 young entrepreneurs. We want to be become out of the league company delivering fabulous and beautiful serviced offices in India and abroad. We hire designers who have made spaces across the world. We want to get visiting card design which gives complete fresh look to the people who carries that card, has to be very impactful and should symbolise happy young and energetic brand. should be completely out of the box thinking of international level, should portray global brand image.

Target Market(s)

Startups, (Small, medium and large corporates)

Industry/Entity Type

Business

Contact Information for Business Card

Name, Email, Address, Mobile number, Landline number, website

Colors

Designer to choose colors to be used in the design.

Requirements
Must have
• Nice new shape
Nice to have
• We want creative cuts, different size and impactful brand clarity
Should not have
• Boring and regular design and shape

```html
<!DOCTYPE html>
<html lang="en">
<head>
<meta charset="utf-8">
<title>Brevlo Business Card</title>
<link href="https://fonts.googleapis.com/css2?family=Lato:wght@400;700;900&display=swap" rel="stylesheet">
<style>
  :root {
    --backdrop: #e4e4e2;
    --card-top: #2b2b2b;
    --card-bottom: #121212;
    --accent: #e3202a;
    --ink-light: #f2f2f2;
  }
  html, body {
    margin: 0;
    padding: 0;
    width: 1200px;
    height: 675px;
    overflow: hidden;
    background: var(--backdrop);
  }
  .stage {
    position: relative;
    width: 1200px;
    height: 675px;
    font-family: "Lato", sans-serif;
  }
  .card-shape {
    position: absolute;
    left: 0;
    top: 0;
  }
  .card-content {
    position: absolute;
    left: 472px;
    top: 97px;
    width: 256px;
    text-align: center;
    color: var(--ink-light);
  }
  .brand-name {
    position: absolute;
    left: 0;
    top: 189px;
    width: 100%;
    margin: 0;
    font-size: 32px;
    font-weight: 900;
    letter-spacing: 4px;
    color: var(--accent);
    line-height: 1;
  }
  .brand-rule {
    position: absolute;
    left: 37px;
    top: 225px;
    width: 178px;
    height: 2px;
    background: var(--accent);
  }
  .tagline {
    position: absolute;
    left: 0;
    top: 234px;
    width: 100%;
    margin: 0;
    font-size: 10px;
    font-weight: 700;
    letter-spacing: 2.2px;
    color: var(--accent);
  }
  .person-name {
    position: absolute;
    left: 0;
    top: 266px;
    width: 100%;
    margin: 0;
    font-size: 19px;
    font-weight: 700;
    color: var(--accent);
    line-height: 1.1;
  }
  .person-role {
    position: absolute;
    left: 0;
    top: 289px;
    width: 100%;
    margin: 0;
    font-size: 12px;
    line-height: 1.1;
  }
  .divider {
    position: absolute;
    left: 113px;
    width: 30px;
    height: 2px;
    background: var(--accent);
  }
  .divider.upper { top: 311px; }
  .divider.lower { top: 371px; }
  .contact-list {
    position: absolute;
    left: 0;
    top: 320px;
    width: 100%;
    margin: 0;
    padding: 0;
    list-style: none;
    font-size: 12px;
    line-height: 15px;
  }
  .contact-label {
    color: var(--accent);
    font-weight: 700;
  }
  .social-row {
    position: absolute;
    left: 83px;
    top: 384px;
  }
</style>
</head>
<body>
<main class="stage">
  <svg class="card-shape" width="1200" height="675" viewBox="0 0 1200 675" aria-hidden="true">
    <defs>
      <linearGradient id="card-fill" x1="0" y1="0" x2="0" y2="1">
        <stop offset="0" stop-color="#2b2b2b"/>
        <stop offset="1" stop-color="#121212"/>
      </linearGradient>
    </defs>
    <path fill="url(#card-fill)"
      d="M486,97 H568 V226 A29,29 0 0 0 626,226 V97 H714 Q728,97 728,111 V530 Q728,544 714,544 H486 Q472,544 472,530 V111 Q472,97 486,97 Z"/>
  </svg>

  <section class="card-content">
    <h1 class="brand-name">BREVLO</h1>
    <div class="brand-rule"></div>
    <p class="tagline">PLAN. MEET. GROW.</p>

    <h2 class="person-name">ARJUN MEHRA</h2>
    <p class="person-role">CEO/FOUNDER</p>

    <div class="divider upper"></div>
    <ul class="contact-list">
      <li>Building 4C, Tech Park, Pune</li>
      <li><span class="contact-label">P</span>: +91 8123456780 <span class="contact-label">C</span>: +91 9000012345</li>
      <li><span class="contact-label">E</span>: arjun@brevlo.in <span class="contact-label">W</span>: www.brevlo.in</li>
    </ul>
    <div class="divider lower"></div>

    <svg class="social-row" width="90" height="20" viewBox="0 0 90 20" aria-hidden="true">
      <g fill="none" stroke="#e3202a" stroke-width="1.2">
        <circle cx="11" cy="10" r="9"/>
        <circle cx="33" cy="10" r="9"/>
        <circle cx="55" cy="10" r="9"/>
        <circle cx="77" cy="10" r="9"/>
      </g>
    </svg>
  </section>
</main>
</body>
</html>
```